We need a business card design for a new company located in Missouri City, TX, entitled 'BrightPath Chiropractic & Holistic Center'. Our services include restoration of health and vitality, spinal exam, health assessment, dietary & fitness programs, lymphatic & therapeutic massage, detox & remineralize body wraps, far infrared sauna therapy

Industry/Entity Type

Business

Contact Information for Business Card

BrightPath Chiropractic & Holistic Center, Marlene Okafor LMT, 4215 Elm Ridge Rd., Suite 310, Missouri City, TX 77482, 281-555-0193

```html
<!DOCTYPE html>
<html lang="en">
<head>
<meta charset="utf-8">
<title>BrightPath Chiropractic &amp; Holistic Center – Business Card</title>
<link rel="stylesheet" href="https://fonts.googleapis.com/css2?family=Old+Standard+TT:wght@400;700&family=Open+Sans:wght@400&display=swap">
<style>
  :root {
    --page: #e4e4e4;
    --ink: #000000;
    --teal: #1ba38c;
    --teal-text: #1a9a85;
    --white: #ffffff;
    --serif: "Old Standard TT", Georgia, serif;
    --sans: "Open Sans", Arial, sans-serif;
  }
  * { margin: 0; padding: 0; box-sizing: border-box; }
  html, body { width: 1189px; height: 1200px; overflow: hidden; background: var(--page); }
  .card {
    position: absolute; left: 140px; width: 917px; height: 522px;
    background: var(--ink); overflow: hidden;
    box-shadow: 0 4px 12px rgba(0,0,0,.35);
  }
  .card--front { top: 47px; }
  .card--back { top: 624px; }

  /* front */
  .front__band {
    position: absolute; left: 0; right: 0; top: 241px; bottom: 0;
    background: var(--teal); border-top: 6px solid var(--white);
  }
  .holder { position: absolute; right: 39px; top: 48px; text-align: right; }
  .holder__name { font-family: var(--serif); font-size: 52px; color: var(--teal); line-height: 1; letter-spacing: 1px; }
  .holder__title { font-family: var(--serif); font-size: 29px; color: var(--white); margin-top: 10px; letter-spacing: .5px; }

  .brand { position: absolute; left: 20px; width: 500px; top: 390px; text-align: center; color: var(--white); }
  .brand__name { font-family: var(--serif); font-size: 48px; line-height: 1; }
  .brand__tagline { font-family: var(--sans); font-size: 25px; margin-top: 8px; }

  .contact { position: absolute; right: 40px; top: 262px; list-style: none; font-family: var(--sans); font-size: 23px; color: var(--white); text-align: right; }
  .contact li { display: flex; justify-content: flex-end; align-items: flex-start; margin-bottom: 8px; line-height: 29px; }
  .contact__icon { width: 19px; height: 19px; margin-left: 8px; margin-top: 6px; flex: none; }
  .contact__address { line-height: 32px; }

  /* back */
  .services { position: absolute; inset: 0; text-align: center; }
  .services__heading {
    position: absolute; top: 18px; left: 51px; right: 51px;
    display: flex; align-items: center; gap: 12px;
    font-family: var(--serif); font-weight: 700; font-size: 56px; color: var(--white);
  }
  .services__heading::before, .services__heading::after { content: ""; flex: 1; height: 2px; background: var(--teal); }
  .services__list { position: absolute; top: 98px; left: 0; right: 0; list-style: none; font-family: var(--serif); font-weight: 700; font-size: 37px; color: var(--teal-text); letter-spacing: .5px; }
  .services__list li { line-height: 57px; }
</style>
</head>
<body>
  <section class="card card--front">
    <div class="front__band"></div>

    <header class="holder">
      <div class="holder__name">Celeste Ramirez</div>
      <div class="holder__title">Chief Executive</div>
    </header>

    <div class="brand">
      <div class="brand__name">BrightPath</div>
      <div class="brand__tagline">Chiropractic &amp; Holistic Center</div>
    </div>

    <ul class="contact">
      <li>281-555-0193
        <svg class="contact__icon" viewBox="0 0 20 20"><rect width="20" height="20" fill="#fff"/><path d="M6 4h3l1 4-2 1c1 2 2 3 4 4l1-2 4 1v3c-6 1-12-5-11-11z" fill="#1ba38c"/></svg>
      </li>
      <li>celeste.ramirez@brightpathcare.com
        <svg class="contact__icon" viewBox="0 0 20 20"><rect width="20" height="20" fill="#fff"/><rect x="3" y="5" width="14" height="10" fill="#1ba38c"/><path d="M3 5l7 6 7-6" stroke="#fff" stroke-width="1.5" fill="none"/></svg>
      </li>
      <li>www.brightpathcare.com
        <svg class="contact__icon" viewBox="0 0 20 20"><rect width="20" height="20" fill="#fff"/><circle cx="10" cy="10" r="6.5" fill="none" stroke="#1ba38c" stroke-width="2"/><path d="M3.5 10h13M10 3.5c-3 3-3 10 0 13M10 3.5c3 3 3 10 0 13" stroke="#1ba38c" stroke-width="1.3" fill="none"/></svg>
      </li>
      <li><span class="contact__address">Marlene Okafor LMT, 4215 Elm Ridge<br>Rd., Suite 310, Missouri City,<br>TX 77482,</span>
        <svg class="contact__icon" viewBox="0 0 20 20"><rect width="20" height="20" fill="#fff"/><path d="M10 16s-5-5-5-8.5a5 5 0 0 1 10 0C15 11 10 16 10 16z" fill="#1ba38c"/><circle cx="10" cy="7.5" r="1.8" fill="#fff"/></svg>
      </li>
    </ul>
  </section>

  <section class="card card--back">
    <div class="services">
      <h2 class="services__heading">Services</h2>
      <ul class="services__list">
        <li>restoration of health and vitality</li>
        <li>spinal exam</li>
        <li>health assessment</li>
        <li>dietary &amp; fitness programs</li>
        <li>lymphatic &amp; therapeutic massage</li>
        <li>detox &amp; remineralize body wraps</li>
        <li>far infrared sauna therapy</li>
      </ul>
    </div>
  </section>
</body>
</html>
```